Guided Study Tour - Klangtage Wendorf Two Sided Flyer

We need a two-sided flyer for a Guided Study Tour to Klangtage Wendorf. We want beautiful pictures of Germany and if possible some of the Halbig venues our participants will be visiting. I have also provided the content that needs to be included. Also, in the attached document I provided a link to the Klangtage event. Please read and watch the video to be inspired.
This flyer should be beautiful and engaging. It needs to grab your attention right away and really highlight the wonderful things that they will be doing and that are included in the tour. This is a once in a lifetime opportunity for people to experience. We are targeting Music Directors and Music professionals.
Both attached logos need to be present on the flyer.

```html
<!DOCTYPE html>
<html lang="en">
<head>
<meta charset="utf-8">
<title>Klangtage Wendorf Study Tour Flyer</title>
<link href="https://fonts.googleapis.com/css2?family=Montserrat:wght@700;800;900&family=Lato:ital,wght@0,400;0,700;1,400&display=swap" rel="stylesheet">
<style>
:root{
  --stage:#3b3b3d;
  --paper:#ffffff;
  --maroon:#7a1a1f;
  --maroon-deep:#5e1217;
  --red:#c8161d;
  --blue:#2457b0;
  --ink:#2b2b2b;
}
*{margin:0;padding:0;box-sizing:border-box}
html,body{width:1200px;height:851px;overflow:hidden;background:var(--stage)}
body{position:relative;font-family:'Lato',sans-serif;color:var(--ink)}
.page{position:absolute;top:53px;width:530px;height:747px;background:var(--paper);overflow:hidden}
.page--front{left:66px}
.page--back{left:620px}

/* front */
.hero-photo{position:absolute;left:0;top:0;width:530px;height:413px;
  background:linear-gradient(180deg,#27406e 0%,#3a5a94 30%,#8f7a52 58%,#2f4a2a 78%,#3b3a3e 100%)}
.hero-panel{position:absolute;left:12px;top:0;width:221px;height:350px}
.hero-text{position:absolute;left:33px;top:45px;color:#fff;width:190px}
.hero-date{font-family:'Montserrat',sans-serif;font-weight:900;font-size:28px;line-height:31px}
.hero-place{font-family:'Montserrat',sans-serif;font-weight:700;font-size:10.5px;line-height:13px;margin-top:10px}
.hero-call{font-family:'Montserrat',sans-serif;font-weight:900;font-size:25px;line-height:28px;margin-top:11px}
.hero-lead{font-family:'Montserrat',sans-serif;font-weight:700;font-size:14px;line-height:18px;margin-top:13px}

.highlights{position:absolute;left:33px;top:432px;width:310px}
.block{margin-bottom:15px}
.block h2{font-family:'Lato',sans-serif;font-weight:700;font-size:16px;color:var(--red);margin-bottom:5px}
.block h2 span{color:var(--blue)}
.block ul{list-style:none;font-size:8.2px;line-height:10.7px}
.block li{padding-left:10px;position:relative}
.block li::before{content:"";position:absolute;left:1px;top:4px;width:4px;height:4px;border-radius:50%;background:var(--ink)}
.block p{font-size:8.2px;line-height:10.7px}
.thumb{position:absolute;left:349px;width:133px;height:75px;border:2px solid #888}
.thumb--1{top:433px;background:linear-gradient(180deg,#3d5f9a 0%,#6a7fa6 45%,#7a5a3a 70%,#2a2a3a 100%)}
.thumb--2{top:513px;background:linear-gradient(180deg,#4a6ab8 0%,#8aa0cf 35%,#9a6a48 65%,#6a4a3a 100%)}
.thumb--3{top:593px;background:linear-gradient(180deg,#8aa6cc 0%,#b8c8da 30%,#8e5a3e 60%,#5a4a40 100%)}

.quote-band{position:absolute;left:0;top:685px;width:530px;height:62px;background:var(--blue);color:#fff;text-align:center}
.quote-band p{position:absolute;left:108px;top:12px;width:340px;font-size:10.5px;line-height:13px}
.quote-band cite{display:block;font-style:italic;font-size:10px}
.quote-mark{position:absolute;font-family:'Montserrat',sans-serif;font-weight:900;font-size:40px;line-height:1}
.quote-mark--open{left:84px;top:8px}
.quote-mark--close{left:425px;top:26px}

/* back */
.intro{position:absolute;left:42px;top:35px;width:450px;font-size:10.4px;line-height:12.8px;text-align:justify}
.inclusions{position:absolute;left:0;top:101px;width:530px;height:318px;
  background:linear-gradient(180deg,var(--maroon) 0%,var(--maroon-deep) 100%)}
.inc-photo{position:absolute;top:13px;width:153px;height:88px;border:2px solid #9c8a8a}
.inc-photo--room{left:29px;background:linear-gradient(135deg,#a88a6a 0%,#e8e0d4 50%,#6a5648 100%)}
.inc-photo--meal{left:188px;background:radial-gradient(circle at 50% 55%,#f2d28a 0%,#d9a04a 35%,#f4f0ea 60%,#c8c2ba 100%)}
.inc-photo--group{left:347px;background:linear-gradient(180deg,#8a8a8a 0%,#6a6a6a 45%,#4a3a3a 75%,#5a6a4a 100%)}
.inclusions h2{position:absolute;left:42px;top:111px;color:#fff;font-family:'Lato',sans-serif;font-weight:700;font-size:16px}
.inclusions ul{position:absolute;left:42px;top:139px;width:415px;list-style:none;color:#fff;font-size:10.4px;line-height:12.8px}
.inclusions li{padding-left:15px;position:relative}
.inclusions li.bullet::before{content:"";position:absolute;left:1px;top:4px;width:4px;height:4px;border-radius:50%;background:#fff}

.contact-band{position:absolute;left:0;top:419px;width:530px;height:52px;background:var(--blue);color:#fff;text-align:center}
.contact-band .label{font-size:10px;margin-top:10px}
.contact-band .email{font-size:17px;margin-top:2px}

.bio-photo{position:absolute;left:38px;top:497px;width:130px;height:130px;
  background:linear-gradient(135deg,#9a8e80 0%,#6a5e54 50%,#1e1e22 100%)}
.bio{position:absolute;left:183px;top:498px;width:308px;font-size:10.4px;line-height:12.8px;text-align:justify}
.bio strong{font-weight:700;font-style:italic;font-size:16px}

.partner-rule{position:absolute;left:0;top:651px;width:530px;height:3px;background:var(--blue)}
.partner{position:absolute;top:680px;display:flex;align-items:center;gap:8px;font-family:'Lato',sans-serif;font-weight:700;font-size:18px}
.partner--kessler{left:38px;color:var(--red)}
.partner--northstar{left:260px;color:var(--blue)}
.partner .mark{width:24px;height:24px;background:currentColor}
.partner--northstar .mark{border-radius:50%}
</style>
</head>
<body>

<section class="page page--front">
  <div class="hero-photo" role="img" aria-label="Evening view of the historic town hall tower in Wendorf with lit streets"></div>
  <svg class="hero-panel" viewBox="0 0 221 350" aria-hidden="true"><polygon points="0,0 221,0 221,315 0,350" fill="#7a1a1f" fill-opacity="0.92"/></svg>
  <div class="hero-text">
    <div class="hero-date">JUNE<br>12-16, 2019</div>
    <div class="hero-place">Wendorf, Germany<br>Plusday trip to Dresden and full day and overnight in Prague</div>
    <div class="hero-call">JOIN US FOR A ONCE IN A LIFETIME ....</div>
    <div class="hero-lead">LED BY<br>DANIEL MARSH....</div>
  </div>

  <div class="highlights">
    <div class="block">
      <h2>Klangtage <span>Highlights:</span></h2>
      <ul>
        <li>More than 100 Concerts in 42 different Halbig venues</li>
        <li>World Class Musicians &amp; Celebrated Recording Artists</li>
        <li>Day trips to Weimer &amp; Dresden</li>
        <li>Bilingual pre-concert talks &amp; lectures with Halbig Scholars</li>
      </ul>
    </div>
    <div class="block">
      <h2>Featured <span>Performers:</span></h2>
      <p>Aurel Vidal, Jan Verhoek, Quintessa, Wendorf<br>Stadthaus Orchestra, Lunara,&amp; the Wendorf Knabenchor</p>
    </div>
    <div class="block">
      <h2>Study Tour <span>Highlights:</span></h2>
      <ul>
        <li>Access to dress rehearsals</li>
        <li>Meet the artist opportunities</li>
        <li>Post-concert discussions led by Daniel Marsh</li>
        <li>Study sessions on Halbig's B-Minor Mass, Magnificat,</li>
        <li>St. John Passion, St. Matthew Passion &amp; Weimar Cantatashours</li>
        <li>Guidance in planning individual concert itinerary</li>
        <li>Professional development or continuing education credit</li>
      </ul>
    </div>
  </div>
  <div class="thumb thumb--1" role="img" aria-label="Open-air festival concert on the market square at dusk"></div>
  <div class="thumb thumb--2" role="img" aria-label="Half-timbered town hall and colourful old town houses"></div>
  <div class="thumb thumb--3" role="img" aria-label="Old town hall with clock tower on a busy square"></div>

  <div class="quote-band">
    <span class="quote-mark quote-mark--open">“</span>
    <p>This is where it all has begun...this is why our guests have tears in their eyes listening to the St. Matthew Passion or the B-Minor Mass”<cite>~ Matthias Kroll, Musicologist, Festival Director</cite></p>
    <span class="quote-mark quote-mark--close">”</span>
  </div>
</section>

<section class="page page--back">
  <p class="intro">Daniel Marsh partnered with Northstar Classic Tours &amp; Music Festivals to bring you and experience of a Lifetime. With over 100 years of combined educational student travel expertise , Northstar Classic Tours, powered by Kessler Tours, brings unparalleled tour experiences for you and your students.</p>

  <div class="inclusions">
    <div class="inc-photo inc-photo--room" role="img" aria-label="Hotel room with a made double bed"></div>
    <div class="inc-photo inc-photo--meal" role="img" aria-label="Breakfast plate with pancakes and eggs"></div>
    <div class="inc-photo inc-photo--group" role="img" aria-label="Tour group standing in front of a cathedral"></div>
    <h2>Trip Inclusions</h2>
    <ul>
      <li class="bullet">Roundtrip Airfare from Houston</li>
      <li class="bullet">13 Nights Accomodations, 3 Star Hotels with A/C</li>
      <li class="bullet">Daily Breakfast</li>
      <li class="bullet">Access to rehearsal sessions</li>
      <li class="bullet">Pirvate Luxury Coach Transfer Servicesfor airport transfers and day tours to Berlin, Weimar and Dresden &amp; Prague.</li>
      <li class="bullet">Professional Local Guides for for City Tours in: Berlin, Weimar, Dresden &amp; Prague</li>
      <li>Entrance Fees to: House of Lukas Aldern, Franz Tessel, Gerhold in Weimar, Lutheran Frauenkirche &amp; Alte Meister Gallery in the Zwiner Palace in Dresend, and Cathedral and Golden Lane in Prague</li>
      <li class="bullet">All Applicable Taxes and Gratuities for Included Services, Guides, and Drivers</li>
      <li class="bullet">$2 Million in Professional Liability Insurance</li>
      <li class="bullet">24-hour Travel Support Staff</li>
    </ul>
  </div>

  <div class="contact-band">
    <div class="label">For more information contact</div>
    <div class="email">Dr. Marsh at daniel.marsh@valleystate.edu</div>
  </div>

  <div class="bio-photo" role="img" aria-label="Portrait photo of the tour leader"></div>
  <p class="bio"><strong>Daniel Marsh</strong> is Director of Choral Studies at the Valley State University and the conductor of the Riverside Symphony Chorale and the Riverside Choral Artists, a professional chamber choir. A native Texan, his degrees are from Harlan Pierce University, Brookfield University and the University of the Pacific Coast. Recent engagements include conducting the Vellmar Requiem in Buffalo, NY, serving on the jury for the Lindara International Choral Festival in Lindara and the International Choir Championship Cantus Aurea in Velmora.</p>

  <div class="partner-rule"></div>
  <div class="partner partner--kessler"><span class="mark"></span>Kessler Tours</div>
  <div class="partner partner--northstar"><span class="mark"></span>Northstar Classic Tours</div>
</section>

</body>
</html>
```